Business Card Design for Vintage Jazz

I am a vintage jazz band leader in New York City. My groups play the music of the 1920s, 1930s and 1940s. My website is morvalquist.com for more info on what I do.

I am looking for a two sided business card design that has the look and feel of a really nice business card from the 1930s. I need to convey with the design that my work has that vintage kind of class and style, but also conveys that we are fun and entertaining.

Most importantly it should make a bold staement. If Hal Denbrook had a card, what would it have looked like? I want a card that I feel confident will make an impact and will let people know that my work is te the top that NYC has to offer in vintage jazz..

Note that I have only decided to avoid the "committed payment" option as I have not used this service before. Assuming that I get quality work I will select a design from those presented.

Target Market(s)

people who want to hire my band for events, media, and new fans of the band

Industry/Entity Type

Performing Art

Contact Information for Business Card

Definitely a matte finish, possibly a sort of old style of paper with that brown tint? definitely a thick card.

Requirements
Must have
• FRONT
• My name: Tobin Vashley
• What I do: Bandleader, Guitarist, Vocalist, Songwriter
• Contact Details: morvalquist.com tobin@morvalquist.com 646-555-0148
• BACK
• My Social Media Links:
• facebook.morvalquist.com
• twitter, instagram, linkedin: morvalquist
• I'm also including a photo image I would like to use. The photo's background is not needed, and to be honest isn't really desireable. Just looking to use the image of me.
Nice to have
• I'm attaching which could be used as is, omitted from the card, or altered maybe with text going around the outside of the circle or in some other way. It may need some clean up to the edges of the lettering as we only use it for the website thumbnail.
• If there's space I'd like to include the text "join our mailing list for a free song download: freesong.morvalquist.com" If not perhaps just "Download a Free Song at: freesong.morvalquist.com - something to this end.
Should not have
• anything cartoony. Don't think retro 90s's vision of the swing era, think actual swing era!
• anything modern. Got to look old school
• Try to avoid dark backgrounds. Since we often play in bars and clubs where it is dar, a d
• avoid script fonts.

```html
<!DOCTYPE html>
<html lang="en">
<head>
<meta charset="utf-8">
<title>Tobin Vashley — Business Card</title>
<link rel="stylesheet" href="https://fonts.googleapis.com/css2?family=Josefin+Sans:wght@400;600;700&family=Libre+Baskerville:wght@400;700&display=swap">
<style>
  :root {
    --page-bg: #e9e6e1;
    --paper-tint: #ece2cd;
    --paper-light: #fbf8f1;
    --ink: #141210;
    --ink-soft: #3a342c;
    --rule: #1d1a16;
    --photo-dark: #2e2e2e;
    --photo-light: #d6d6d6;
    --card-shadow: rgba(0, 0, 0, 0.2);
  }
  * { box-sizing: border-box; margin: 0; padding: 0; }
  html, body {
    width: 1200px;
    height: 900px;
    overflow: hidden;
    background: var(--page-bg);
    font-family: "Libre Baskerville", Georgia, serif;
  }
  .sheet {
    width: 1200px;
    height: 900px;
    display: flex;
    align-items: center;
    justify-content: center;
    gap: 40px;
  }
  .card {
    position: relative;
    width: 540px;
    height: 309px;
    box-shadow: 0 10px 26px var(--card-shadow);
    overflow: hidden;
    color: var(--ink);
  }
  .card::before,
  .card::after {
    content: "";
    position: absolute;
    pointer-events: none;
  }
  .card::before { inset: 12px; border: 2px solid var(--rule); }
  .card::after { inset: 17px; border: 1px solid var(--rule); }

  /* Back side */
  .card--back { background: var(--paper-tint); }
  .social-list {
    position: absolute;
    top: 34px;
    left: 360px;
    list-style: none;
    font-family: "Josefin Sans", Arial, sans-serif;
    font-size: 13px;
    line-height: 19px;
    letter-spacing: 0.03em;
  }
  .social-list li { display: flex; align-items: center; gap: 7px; }
  .social-list .marker {
    width: 9px;
    height: 9px;
    background: var(--ink);
    flex: none;
  }
  .monogram {
    position: absolute;
    left: 62px;
    top: 176px;
    display: flex;
    align-items: center;
    gap: 12px;
    font-family: "Josefin Sans", Arial, sans-serif;
    font-size: 22px;
    font-weight: 600;
    letter-spacing: 0.12em;
    text-transform: uppercase;
  }
  .monogram .dot {
    width: 48px;
    height: 48px;
    border: 2px solid var(--ink);
    border-radius: 50%;
    flex: none;
  }

  /* Front side */
  .card--front { background: var(--paper-light); }
  .portrait {
    position: absolute;
    left: 44px;
    top: 60px;
    width: 240px;
    height: 249px;
    background: linear-gradient(160deg, var(--photo-light) 0%, #7a7a7a 35%, var(--photo-dark) 70%, #1a1a1a 100%);
    border-radius: 110px 110px 0 0;
  }
  .details {
    position: absolute;
    left: 296px;
    top: 40px;
    width: 220px;
  }
  .details__name {
    font-family: "Josefin Sans", Arial, sans-serif;
    font-size: 21px;
    font-weight: 700;
    letter-spacing: 0.08em;
    text-transform: uppercase;
    margin: 0 0 12px 16px;
    white-space: nowrap;
  }
  .details__contact {
    font-size: 10.5px;
    line-height: 16px;
    color: var(--ink-soft);
    white-space: nowrap;
  }
  .details__contact b {
    font-family: "Josefin Sans", Arial, sans-serif;
    font-size: 12px;
    font-weight: 700;
    letter-spacing: 0.04em;
    color: var(--ink);
  }
  .details__role {
    margin-top: 14px;
    font-family: "Josefin Sans", Arial, sans-serif;
    font-size: 15px;
    line-height: 19px;
    font-weight: 600;
    letter-spacing: 0.05em;
    text-transform: uppercase;
  }
</style>
</head>
<body>
<main class="sheet">
  <section class="card card--back" aria-label="Card back">
    <ul class="social-list">
      <li><span class="marker"></span>morvalquist.com</li>
      <li><span class="marker"></span>morvalquist</li>
      <li><span class="marker"></span>morvalquist</li>
      <li><span class="marker"></span>morvalquist</li>
    </ul>
    <div class="monogram"><span class="dot"></span>Tobin Vashley</div>
  </section>

  <section class="card card--front" aria-label="Card front">
    <div class="portrait" role="img" aria-label="Black and white photo of the bandleader in a trimmed blazer and cravat, tipping a straw boater hat"></div>
    <div class="details">
      <h1 class="details__name">Tobin Vashley</h1>
      <p class="details__contact"><b>Phone:</b> 646-555-0148</p>
      <p class="details__contact"><b>Email:</b> tobin@morvalquist.com</p>
      <p class="details__contact"><b>Website:</b> morvalquist.com</p>
      <p class="details__role">Bandleader, Guitarist,<br>Vocalist, Songwriter</p>
    </div>
  </section>
</main>
</body>
</html>
```